Flyer Rework for Accountants and Lawyers

Information flyer for accountants and lawyers. Text and flowchart provided. Just need to make it look presentable for print and email. Needs to add logo (AI file provided) and provide graphics. No more than two pages. Our corporate visual identify guidelines are attached (MUST Use). Completed on both AI file and PPTX file.
Target Market(s)
Accountants, Company Directors and Lawyers
Industry/Entity Type
Finance And Accounting
Requirements
Must have
- Our corporate visual identify guidelines are attached (MUST Use)

```html
<!DOCTYPE html>
<html lang="en">
<head>
<meta charset="utf-8">
<title>Northpoint Advisory – Director Penalty Notices</title>
<link href="https://fonts.googleapis.com/css2?family=Roboto:wght@400;500;700&family=Roboto+Condensed:wght@400&display=swap" rel="stylesheet">
<style>
:root{
  --backdrop:#bdbec0;
  --paper:#ffffff;
  --green:#8cc63f;
  --green-light:#a3d15a;
  --cyan:#5fc8dd;
  --cyan-pale:#78d0e2;
  --charcoal:#58595b;
  --slate:#6d6e70;
  --ink:#3b3b3d;
  --row-a:#f1f1f2;
  --row-b:#e6e7e8;
}
*{box-sizing:border-box;margin:0;padding:0}
html,body{width:1200px;height:990px;overflow:hidden}
body{background:var(--backdrop);font-family:"Roboto",Arial,sans-serif;color:var(--ink);position:relative}
.page{position:absolute;top:155px;width:524px;height:679px;background:var(--paper);overflow:hidden}
.page--front{left:63px}
.page--back{left:618px}
.abs{position:absolute}

/* brand */
.brand{display:flex;align-items:center;gap:6px}
.brand__dot{width:14px;height:14px;border-radius:50%;background:var(--green)}
.brand__name{font-size:11px;font-weight:500;color:var(--green);letter-spacing:.3px;text-transform:uppercase}

.contact{left:377px;top:24px;font-size:9px;line-height:14.5px;color:var(--ink)}
.contact li{list-style:none;display:flex;align-items:center;gap:6px}
.contact svg{width:8px;height:8px}
.contact strong{font-weight:700}

.hero{left:0;top:87px;width:524px;height:167px;
  background:linear-gradient(180deg,#3f8fc4 0%,#7fb6d8 35%,#f0b15a 58%,#2f8fc8 72%,#44b6e4 100%)}
.hero__tag{left:32px;top:116px;font-family:"Roboto Condensed",Arial,sans-serif;font-size:16px;color:#fff;letter-spacing:.2px}

.intro-band{left:0;top:254px;width:524px;height:56px;background:var(--slate);color:#fff;font-size:10px;line-height:12px;padding:10px 32px 0 33px}

.section-title{font-size:16px;font-weight:700;color:var(--green)}
.body-copy{font-size:10px;line-height:12px;color:var(--ink)}

.facts{left:33px;top:431px;width:463px;border-collapse:collapse;font-size:8px;line-height:10px}
.facts th{background:var(--green-light);color:#fff;font-size:12px;font-weight:500;text-align:left;height:21px;padding:0 9px}
.facts th:first-child{width:152px;border-right:2px solid #fff}
.facts td{vertical-align:top;padding:6px 9px 5px}
.facts td:first-child{font-weight:700;border-right:2px solid #fff;padding-left:11px}
.facts tr:nth-child(odd) td{background:var(--row-a)}
.facts tr:nth-child(even) td{background:var(--row-b)}
.facts ul{margin:5px 0 0 20px}
.facts li{list-style:disc;line-height:10.5px}

.footer-band{left:0;top:656px;width:524px;height:23px;font-size:9px;letter-spacing:2px;color:var(--charcoal);text-align:center;line-height:23px}
.footer-band--cyan{background:var(--cyan)}
.footer-band--green{background:var(--green-light)}

/* back page */
.tips{left:0;top:0;width:524px;height:219px;background:linear-gradient(135deg,var(--cyan-pale),var(--cyan))}
.tips__bar{left:0;top:38px;width:358px;height:22px;background:var(--charcoal);color:#fff;font-size:12px;font-weight:700;line-height:22px;padding-left:51px}
.tips__list{left:74px;top:72px;width:390px;color:#fff;font-size:10px;line-height:11.6px;padding-left:14px}
.tips__list li{margin-bottom:7px}

.flow-box{position:absolute;color:#fff;font-size:7px;line-height:8.4px;padding:0 8px;display:flex;flex-direction:column;justify-content:center;border-radius:3px}
.flow-box--green{background:var(--green-light)}
.flow-box--cyan{background:var(--cyan)}
.flow-box--dark{background:var(--charcoal)}
.flow-box ol{padding-left:0;list-style:none}
.flow-svg{position:absolute;left:0;top:0}
.flow-label{font-family:"Roboto",Arial,sans-serif;font-size:8px;font-weight:700;fill:var(--ink)}

.help-title{font-size:16px;font-weight:700;color:var(--cyan)}
.cta{left:0;top:548px;width:524px;text-align:center;font-size:10px;line-height:12px}
</style>
</head>
<body>

<section class="page page--front">
  <div class="abs brand" style="left:34px;top:36px">
    <span class="brand__dot"></span><span class="brand__name">Northpoint Advisory</span>
  </div>
  <ul class="abs contact">
    <li><svg viewBox="0 0 10 10"><circle cx="5" cy="5" r="4" fill="none" stroke="#6d6e70" stroke-width="1.2"/></svg>www.npadvisory.com.au</li>
    <li><svg viewBox="0 0 10 10"><rect x="1" y="2" width="8" height="6" fill="#6d6e70"/></svg>info@npadvisory.com.au</li>
    <li><svg viewBox="0 0 10 10"><path d="M3 1 L5 3 L4 4.5 Q5 6 6 6.5 L7.5 5.5 L9 7.5 L7.5 9 Q3 8 1 2.5 Z" fill="#58595b"/></svg><strong>(02) 5550 1234</strong></li>
  </ul>

  <div class="abs hero" role="img" aria-label="Photograph of a harbour city skyline and arch bridge at sunset"></div>
  <p class="abs hero__tag">INDEPENDENT. CONCISE. EFFICIENT.</p>

  <p class="abs intro-band">Company directors and their advisors need to be aware that non-lodgement of Business Activities Statements (“BAS”) and Superannuation Guarantee Charge (“SCG”) Statements with the ATO may be personally liability for these debts.</p>

  <h2 class="abs section-title" style="left:34px;top:327px">Director Penalty Notices (“DPN”)</h2>
  <p class="abs body-copy" style="left:33px;top:354px;width:460px">The ATO uses DPNs and Garnishee Notices to recovery tax debts and to impose positive obligations on Directors to deal with outstanding PAYG Withholding and the Superannuation Guarantee Charge debts (“Tax Debts”).</p>
  <p class="abs body-copy" style="left:33px;top:393px;width:460px">The DPN regime makes directors of companies who fail to pay Tax Debts personally liable. The key facts of DPN regime are outlined below:</p>

  <table class="abs facts">
    <tr><th>Facts</th><th>Key facts of a Directors Penalty Notice</th></tr>
    <tr><td>1.&nbsp; Director personal liabilities</td><td>Directors become personally liable for Tax Debts 21 days are the DPN Notice is issued</td></tr>
    <tr><td>2.&nbsp; Automatic liability for unreported and unpaid Tax Debts</td><td>Where a company's Tax Debts were both unreported and unpaid 3 months after the due date, the directors are automatically personally liable for the Tax Debts.</td></tr>
    <tr><td>3.&nbsp; Avoiding personal liability for directors once they receive a DPN</td><td>Within 21 days of issuing the DPN (which may be received a week or more after issue), a director can avoid personal liability by either:
      <ul><li>Paying the Tax Debt</li><li>Appointing an Administrator to the company</li><li>Appointing a Liquidator to the company.</li></ul></td></tr>
    <tr><td>4.&nbsp; Effect on new directors</td><td>New directors are liable if outstanding Tax Debts are unpaid 30 days after their appointment as director</td></tr>
    <tr><td>5.&nbsp; Time frames</td><td>ATO can only enforce a DPN after 21 days of giving notice to the director and notice can be given to the company tax agent</td></tr>
  </table>

  <div class="abs footer-band footer-band--cyan">www.npadvisory.com.au</div>
</section>

<section class="page page--back">
  <div class="abs tips" role="img" aria-label="Cyan-tinted photograph of people in a business meeting"></div>
  <h2 class="abs tips__bar">Tips for directors to limit or avoid personal liability:</h2>
  <ol class="abs tips__list">
    <li>Always lodge BAS and SGC Statements within 3 months of the due date, even if the liability cannot be paid!</li>
    <li>Act immediately upon receipt of a DPN and consider a payment arrangement with the ATO. This should be considered with care as payments made can be considered as preference payments to the ATO, if a liquidator is appointed. The ATO can make the directors personally liable for the ATO preference claim</li>
    <li>Seek professional advice from an insolvency practitioner about the options available and possibly save the company through a financial restructure.</li>
  </ol>

  <h2 class="abs" style="left:41px;top:240px;font-size:16px;font-weight:700;color:var(--charcoal)">Summary of the DPN</h2>

  <svg class="flow-svg" width="524" height="460" viewBox="0 0 524 460" aria-hidden="true">
    <g fill="var(--green-light)">
      <path d="M126 349h12v-4l8 7-8 7v-4h-12z"/>
      <path d="M351 298h10v-4l8 7-8 7v-4h-10z"/>
      <path d="M430 350h6v11h4l-7 8-7-8h4z"/>
      <path d="M379 348h6v58h-28v4l-8-7 8-7v4h22z"/>
      <path d="M239 318l12-9-2-3 9-1-3 8-2-2-12 9z" fill="var(--cyan)"/>
      <path d="M239 381l12 8-2 2 9 1-3-8-2 2-12-8z" fill="var(--cyan)"/>
    </g>
    <text class="flow-label" x="244" y="302">NO</text>
    <text class="flow-label" x="240" y="374">YES</text>
    <text class="flow-label" x="452" y="361">YES</text>
    <text class="flow-label" x="366" y="400">NO</text>
  </svg>

  <div class="flow-box flow-box--green" style="left:38px;top:320px;width:86px;height:69px">Issued Director's Penalty Notice By ATO</div>
  <div class="flow-box flow-box--cyan" style="left:150px;top:301px;width:85px;height:107px">Business Activity Statement and Superannuation Guarantee Charge lodged within 3 months from due date</div>
  <div class="flow-box flow-box--dark" style="left:261px;top:278px;width:85px;height:68px">Director not personally liable yet.<br>(Have options)</div>
  <div class="flow-box flow-box--dark" style="left:261px;top:367px;width:85px;height:69px">Director Automatically personally liable</div>
  <div class="flow-box flow-box--green" style="left:372px;top:257px;width:113px;height:91px">If Directors act within 21 days and:
    <ol><li>1. Wind up Company voluntarily; or</li><li>2. Appoint Voluntary Administrator; or</li><li>3. Pay debt in full</li></ol></div>
  <div class="flow-box flow-box--green" style="left:400px;top:370px;width:85px;height:68px">Director not personally liable but the company is still insolvent.</div>

  <h2 class="abs help-title" style="left:39px;top:458px">How Northpoint Advisory can help?</h2>
  <p class="abs body-copy" style="left:39px;top:486px;width:455px">Northpoint Advisory is a firm that specialises in insolvency and restructuring, we are here to assist your clients who experiencing financial difficulties with straight forward solutions in simple to understand terms.&nbsp; The initial consultation is free, strictly confidential and without obligation.</p>
  <p class="abs cta">Please call <strong>(02) 5550 1234</strong> to speak to one of our solvency specialistor<br>email <strong>info@npadvisory.com.au</strong></p>

  <div class="abs brand" style="left:182px;top:611px">
    <span class="brand__dot"></span><span class="brand__name">Northpoint Advisory</span>
  </div>

  <div class="abs footer-band footer-band--green">www.npadvisory.com.au</div>
</section>

</body>
</html>
```